Creative, fresh business card design for Ripplecraft Facades

We need a fresh, creative business card design for Ripplecraft Facades. We are the manufacturer of Ripplecraft Facades in Australia. Wall panels are 2400 x 1200mm panels made from MDF and feature 3D patterns on the face of the panel. The colours to be used are green, silver/grey and white RGB
Red 187
Green 207
Blue 65.

An idea is to possibly use a watermark of one of our designs as a background (like on the "Grids" design on the left hand side of page 2 of our brochure).

Target Market(s)

Interior designers, architects, builders and home renovators

Industry/Entity Type

Business

Contact Information for Business Card

Details to go on the card are:
Our logo (attached),
Slogan: "Decorative panels for interiors and exteriors",
Contact name,
Position,
Mobile phone number,
Business address,
Business phone,
Business fax,
Website and
Email address.

I have attached a few images of our panels and our brochure for reference.

The colours of the business card should feature our logo colours which are: RGB
Red 187
Green 207
Blue 65

Requirements
Must have
• Very modern fonts and design. Some of the designs shown especially the "Prisms" design which is a popular design.
Nice to have
• Creative but simple design. Very contemporary.
Should not have
• Anything ornate or old fashioned.

```html
<!DOCTYPE html>
<html lang="en">
<head>
<meta charset="utf-8">
<title>Ripplecraft Facades – Business Card</title>
<link rel="stylesheet" href="https://fonts.googleapis.com/css2?family=Open+Sans:wght@400;600;700&display=swap">
<style>
  :root {
    --backdrop: #e6e2dc;
    --card-top: #2c2c2c;
    --card-bottom: #1f1f1f;
    --brand-green: #afbf35;
    --text-light: #cfcfcf;
    --text-muted: #8c8c8c;
    --divider: #6f6a55;
  }
  * { margin: 0; padding: 0; box-sizing: border-box; }
  html, body {
    width: 1200px;
    height: 1000px;
    overflow: hidden;
    background: var(--backdrop);
    font-family: "Open Sans", Arial, sans-serif;
  }
  .business-card {
    position: absolute;
    left: 150px;
    top: 265px;
    width: 950px;
    height: 515px;
    border-radius: 22px;
    background: linear-gradient(180deg, var(--card-top), var(--card-bottom));
    box-shadow: 0 10px 30px rgba(0,0,0,0.25);
  }
  .brand {
    position: absolute;
    left: 170px;
    top: 178px;
    width: 250px;
    display: flex;
    align-items: center;
    gap: 12px;
  }
  .brand-square {
    width: 22px;
    height: 22px;
    background: var(--brand-green);
    flex-shrink: 0;
  }
  .brand-name {
    color: var(--brand-green);
    font-size: 25px;
    font-weight: 700;
    line-height: 1.15;
  }
  .slogan {
    position: absolute;
    left: 172px;
    top: 326px;
    width: 250px;
    color: var(--text-muted);
    font-size: 14px;
    letter-spacing: 2.2px;
    line-height: 17px;
    text-align: center;
  }
  .divider {
    position: absolute;
    left: 459px;
    top: 130px;
    width: 2px;
    height: 275px;
    background: var(--divider);
  }
  .contact-block {
    position: absolute;
    left: 510px;
    top: 122px;
  }
  .person-name {
    color: var(--brand-green);
    font-size: 29px;
    font-weight: 700;
    letter-spacing: 0.5px;
    line-height: 36px;
  }
  .person-role {
    color: var(--text-light);
    font-size: 19px;
    line-height: 26px;
  }
  .address {
    margin-top: 14px;
    color: var(--text-light);
    font-size: 19px;
    line-height: 25px;
    letter-spacing: 0.4px;
  }
  .contact-list {
    list-style: none;
    margin-top: 20px;
  }
  .contact-list li {
    display: flex;
    align-items: center;
    height: 29px;
    color: var(--text-muted);
    font-size: 19px;
    letter-spacing: 0.5px;
  }
  .contact-icon {
    width: 16px;
    height: 16px;
    margin-right: 23px;
    fill: var(--brand-green);
    flex-shrink: 0;
  }
  .web-highlight { color: var(--brand-green); }
</style>
</head>
<body>
  <div class="business-card">
    <div class="brand">
      <span class="brand-square"></span>
      <span class="brand-name">Ripplecraft Facades</span>
    </div>
    <p class="slogan">decorative panels for<br>interiors &amp; landscapes</p>

    <div class="divider"></div>

    <div class="contact-block">
      <h1 class="person-name">Dana Whitford</h1>
      <p class="person-role">Director</p>
      <p class="address">Your Street Address,<br>New York, 1234</p>
      <ul class="contact-list">
        <li>
          <svg class="contact-icon" viewBox="0 0 16 16" aria-hidden="true"><path d="M4 0h8a1 1 0 0 1 1 1v14a1 1 0 0 1-1 1H4a1 1 0 0 1-1-1V1a1 1 0 0 1 1-1zm1 2v10h6V2zm3 11a1 1 0 1 0 0 2 1 1 0 0 0 0-2z"/></svg>
          +000 123 456 789
        </li>
        <li>
          <svg class="contact-icon" viewBox="0 0 16 16" aria-hidden="true"><path d="M3.5 1l2.5 3-1.5 2c1 2 3 4 5 5l2-1.5 3 2.5-1.5 3C7 15 1 9 .5 2.5z"/></svg>
          +000 123 456 789
        </li>
        <li>
          <svg class="contact-icon" viewBox="0 0 16 16" aria-hidden="true"><path d="M4 1h7v4H4zM1 6h14v8H1zm2 2v2h2V8zm4 0v2h2V8zm4 0v2h2V8z"/></svg>
          +000 123 456 789
        </li>
        <li>
          <svg class="contact-icon" viewBox="0 0 16 16" aria-hidden="true"><path d="M0 3h16v10H0zm1.5 1.5v.4L8 9l6.5-4.1v-.4zM1.5 6.6v4.9h13V6.6L8 10.7z"/></svg>
          yourname@email.com
        </li>
        <li>
          <svg class="contact-icon" viewBox="0 0 16 16" aria-hidden="true"><path d="M10 1a5 5 0 1 1 0 10 5 5 0 0 1 0-10zm0 2a3 3 0 1 0 0 6 3 3 0 0 0 0-6zM5.2 9.4l1.4 1.4-4.4 4.4-1.4-1.4z"/></svg>
          www.<span class="web-highlight">websitename</span>.com
        </li>
      </ul>
    </div>
  </div>
</body>
</html>
```